Morvane Capital, a private equity fund, needs a brochure

Morvane Capital is a private equity fund dedicated to the development of budget hotels in France (reasonably priced hotel rooms).
Our customers are French private and high-income investors.

The brochure should communicate :
- seriousness and expertise
- trust, confidence and security
- financial product and profitability

The title is : Investissez dans l'hôtellerie économique et l'immobilier

Brochure size :
3 pages A4
Open size : 63 x 29,7 cm
Closed size : 21 x 29,7 cm

Our competitors :
Trelisse http://trelisse-immo-horizon.example/
789 Parcours http://www.789parcours.example/
GLD Capital http://www.gldam.example/
Soltane capital http://www.soltanecapital.example/
Barostel http://www.barostel.example/

Target Market(s)

Private investors, high-income ; Institutional investors ; Target customers are French private investors with high revenue.

Industry/Entity Type

Financial

Requirements
Must have
• - Brochure must respect our identity (you can see our logo) and use its colors and typo (and/or same typo style)
- You must use pictures on each interior pages (pictures of projetc and hotels)

```html
<!DOCTYPE html>
<html lang="fr">
<head>
<meta charset="utf-8">
<title>Morvane Capital – Trois sources potentielles de gains</title>
<link href="https://fonts.googleapis.com/css2?family=Roboto+Condensed:wght@400;700&family=Arimo:wght@400;700&display=swap" rel="stylesheet">
<style>
:root{
  --bg:#d9dcdf;
  --paper:#ffffff;
  --ink:#2b2b2b;
  --red:#b0191e;
  --red-deep:#8e1418;
  --grey:#b9bbbb;
  --grey-label:#c6c7c6;
  --sky:#1ba4e4;
  --blue:#1665ae;
  --navy:#0d3d66;
  --rule:#9a9a9a;
  --black:#1d1d1d;
}
*{margin:0;padding:0;box-sizing:border-box}
html,body{width:900px;height:1200px;overflow:hidden;background:var(--bg)}
body{position:relative;font-family:"Arimo",Arial,sans-serif;color:var(--ink)}
.page{position:absolute;left:59px;top:45px;width:790px;height:1117px;background:var(--paper)}
.abs{position:absolute}
.section-title{font-family:"Roboto Condensed",Arial,sans-serif;font-weight:700;color:var(--red);font-size:14.5px}
.body-text{font-size:12.2px;line-height:16px;text-align:justify}
.bullets{list-style:none;font-weight:700;font-size:12.2px;line-height:16px}
.bullets li{position:relative;padding-left:15px}
.bullets li::before{content:"";position:absolute;left:0;top:5px;width:7px;height:7px;background:var(--red)}
.photo{position:absolute;border:1px solid #bbb}
.photo-hotel{background:linear-gradient(180deg,#e8eef2 0%,#dfe6e0 45%,#55704a 75%,#7a8a6c 100%)}
.photo-city{background:linear-gradient(180deg,#e6ecf1 0%,#d4d8dc 50%,#9aa49a 80%,#b6b8b4 100%)}
.photo-resort{background:linear-gradient(180deg,#e3ecef 0%,#b6c8b2 45%,#4a6a3c 75%,#6b7d57 100%)}
.caption{font-size:10.5px;line-height:15px}
.caption b{font-weight:700}
.disclaimer{border-top:2px solid var(--rule);border-bottom:2px solid var(--rule);font-size:10.4px;line-height:15.2px;text-align:justify;padding:10px 0 6px}
.dot-list{list-style:none;font-size:12.2px;line-height:16px}
.dot-list li{position:relative;text-indent:15px;margin-bottom:13px;text-align:justify}
.dot-list li::before{content:"";position:absolute;left:-15px;top:5px;width:7px;height:7px;background:var(--red)}
.share-title{font-family:"Arimo",Arial,sans-serif;font-weight:700;font-size:12.2px}
.bar{position:absolute;background:var(--red);color:#fff;font-family:"Arimo",Arial,sans-serif;font-weight:700;text-align:center}
.bar-label{position:absolute;font-weight:700;font-size:12.2px;text-align:center;display:flex;align-items:center;justify-content:center}
.bar-label.grey{background:var(--grey-label);color:var(--black)}
.bar-label.dark{background:var(--black);color:#fff}
.foot-rule{position:absolute;left:0;right:0;top:1050px;border-top:1px solid var(--rule)}
</style>
</head>
<body>
<div class="page">
  <h2 class="section-title abs" style="left:39px;top:80px">Trois sources potentielles de gains:</h2>
  <p class="body-text abs" style="left:39px;top:114px;width:461px">Une double plus-value potentielle hôtelière et immobilière assortie d’un rendement annuel. La création de valeur pour chacun des hôtels dans lesquels MORVANE CAPITAL prendra des participations proviendra de la valorisation des murs de l’hôtel, de la valorisation de son fonds de commerce et de la rentabilité annuelle de l’exploitation. L’activité de location de meublés de tourisme bénéficie des mêmes synergies.</p>
  <p class="body-text abs" style="left:39px;top:210px;width:461px">La création de valeur pour l’activité de promotion immobilière (construction vente des immeubles) proviendra des marges dégagées par les opérations de promotion.</p>
  <ul class="bullets abs" style="left:39px;top:259px;width:420px">
    <li>Trois sources potentielles de gains, assorties toutefois d’un risque de perte en capital</li>
    <li>Atténuation de risques du fait de l’investissement diversifié dans les murs et dans le fonds de commerce</li>
    <li>Un recours à un financement peu couteux</li>
  </ul>

  <div class="photo photo-hotel" role="img" aria-label="Photo de l’EHPAD en Martinique, bâtiment bas entouré de palmiers" style="left:528px;top:88px;width:208px;height:70px"></div>
  <p class="caption abs" style="left:528px;top:164px"><b>Martinique -</b> EHPAD Ecrin des Alizés,<br>79 chambres</p>
  <div class="photo photo-city" role="img" aria-label="Rendu architectural des Terrasses du Port, immeubles hôteliers en Martinique" style="left:528px;top:218px;width:208px;height:67px"></div>
  <p class="caption abs" style="left:528px;top:292px"><b>Martinique -</b> Les Terrasses du Port<br>Étape Claire, 100 chambres</p>

  <svg class="abs" style="left:0;top:345px" width="790" height="220" viewBox="0 0 790 220" role="img" aria-label="Courbe de gains espérés de 2012 à 2019">
    <rect x="33" y="126" width="147" height="52" fill="#a01a1e"/>
    <polygon points="180,178 180,128 494,28 494,178" fill="#b9bbbb"/>
    <g stroke="#fff" stroke-width="1.5">
      <line x1="243" y1="108" x2="243" y2="178"/><line x1="307" y1="88" x2="307" y2="178"/>
      <line x1="370" y1="68" x2="370" y2="178"/><line x1="433" y1="48" x2="433" y2="178"/>
    </g>
    <line x1="33" y1="178" x2="494" y2="178" stroke="#222" stroke-width="1"/>
    <polyline points="53,172 117,148 180,128 243,108 307,88 370,68 433,48 494,28" fill="none" stroke="#d0202a" stroke-width="2"/>
    <circle cx="53" cy="172" r="5.5" fill="#fff"/><circle cx="117" cy="148" r="5.5" fill="#fff"/>
    <g fill="#c8161e"><circle cx="180" cy="128" r="5.5"/><circle cx="243" cy="108" r="5.5"/><circle cx="307" cy="88" r="5.5"/><circle cx="370" cy="68" r="5.5"/><circle cx="433" cy="48" r="5.5"/></g>
    <text x="38" y="121" font-family="Arimo,Arial,sans-serif" font-weight="700" font-size="12" fill="#111">INVESTISSEMENTS</text>
    <text x="313" y="121" font-family="Arimo,Arial,sans-serif" font-weight="700" font-size="12" fill="#222">Espérance de gains</text>
    <text x="313" y="136" font-family="Arimo,Arial,sans-serif" font-weight="700" font-size="12" fill="#222">pour l’investisseur</text>
    <g font-family="Arimo,Arial,sans-serif" font-weight="700" font-size="12" fill="#111">
      <text x="39" y="196">2012</text><text x="100" y="196">2013</text><text x="161" y="196">2014</text><text x="353" y="196">2017</text><text x="481" y="196">2019</text>
    </g>
    <g font-family="Roboto Condensed,Arial,sans-serif" font-weight="700" font-size="13" fill="#fff">
      <rect x="496" y="5" width="240" height="35" fill="#1ba4e4"/><text x="506" y="28">PLUS VALUES HOTELIÈRES</text>
      <rect x="496" y="45" width="240" height="35" fill="#1665ae"/><text x="506" y="68">PLUS VALUES IMMOBILIÈRES</text>
      <rect x="496" y="86" width="240" height="34" fill="#0d3d66"/><text x="506" y="108">RENDEMENT ANNUEL CAPITALISÉ</text>
      <rect x="496" y="126" width="240" height="52" fill="#a01a1e"/><text x="506" y="148">REMBOURSEMNT</text><text x="506" y="164">DU CAPITAL INITIAL</text>
    </g>
    <line x1="725" y1="20" x2="725" y2="216" stroke="#333" stroke-width="1"/>
    <g fill="#fff" stroke="#333" stroke-width="1"><rect x="721" y="18" width="8" height="8"/><rect x="721" y="58" width="8" height="8"/><rect x="721" y="98" width="8" height="8"/><rect x="721" y="142" width="8" height="8"/></g>
    <text x="719" y="196" text-anchor="end" font-family="Roboto Condensed,Arial,sans-serif" font-size="11" fill="#333">Exonération fiscale</text>
    <text x="719" y="210" text-anchor="end" font-family="Roboto Condensed,Arial,sans-serif" font-size="11" fill="#333">(hors prélèvement sociaux)</text>
  </svg>

  <p class="disclaimer abs" style="left:39px;top:566px;width:460px">L’attention des investisseurs est toutefois attirée sur l’impact de l’effet “moyenne” d’un tel affichage, lequel peut masquer de mauvais résultats pour certains fonds en particulier et lequel ne préjuge pas de performances d’un niveau équivalent pour le présent fond (étant en toutes hypothèses rappelé que Morvane Capital présente un risque de perte en capital). Par ailleurs, l’attention des investisseurs est attirée sur les facteurs de risques liés à un investissement dans Morvane Capital présentés ci-après dans le présent document.</p>

  <div class="photo photo-resort" role="img" aria-label="Photo d’hôtels près de l’aéroport en Guyane, bâtiments dans la végétation" style="left:528px;top:596px;width:208px;height:66px"></div>
  <p class="caption abs" style="left:528px;top:673px"><b>Guyane -</b> Aéroport de Kourelle,<br>Zone des Palmiers-Matoury<br>Bastide Hôtels, 60 chambres<br>Étape Claire, 40 chambres</p>

  <h2 class="section-title abs" style="left:39px;top:736px">Comment sont répartis les gains ?</h2>
  <p class="body-text abs" style="left:39px;top:767px;width:460px">Le capital de la société MORVANE CAPITAL est constitué de deux types de catégorie d’actions A et B.</p>
  <ul class="dot-list abs" style="left:39px;top:816px;width:460px">
    <li>Les actions de type A destinées aux investisseurs.</li>
    <li>Les actions de type B (carried-interest) destinées à être souscrites par les personnes intervenant dans la gestion de MORVANE CAPITAL</li>
    <li>En vertu des dispositions légales et statutaires applicables, l’émission de 100 actions de type A oblige à émettre 1 action B Ne pouvant être souscrite que par les personnes intervenant dans la gestion de MORVANE CAPITAL.</li>
  </ul>
  <p class="body-text abs" style="left:39px;top:960px;width:460px">Les droits préférentiels attachés aux actions A et aux actions B sont définis à l’article 14.2 des statuts de Morvane Capital et répondent notamment au principe selon lequel l’actif net de liquidation au-delà d’un “rendement” de 7% l’an sera réparti à hauteur de 80% pour les actions A (investisseurs) et 20% pour les actions B (personnes intervenant dans la gestion du fonds).</p>

  <h3 class="share-title abs" style="left:514px;top:790px">PARTAGE DE GAINS ESPÉRÉS</h3>
  <div class="bar" style="left:514px;top:817px;width:106px;height:146px;font-size:22px;padding-top:8px">80%</div>
  <div class="bar" style="left:630px;top:928px;width:106px;height:35px;font-size:18px;padding-top:5px">20%</div>
  <div class="bar-label grey" style="left:514px;top:963px;width:106px;height:35px">Investisseur</div>
  <div class="bar-label grey" style="left:630px;top:963px;width:106px;height:35px">Gestionnaire</div>
  <div class="bar-label dark" style="left:514px;top:998px;width:106px;height:35px">Actions A</div>
  <div class="bar-label dark" style="left:630px;top:998px;width:106px;height:35px">Actions B</div>

  <div class="foot-rule"></div>
</div>
</body>
</html>
```